Business card design for Virtual Assistance company

I need a business card designed for my virtual assistance company. We are a small company who services primarily C-level executive clients. The card needs to be double sided with the following contact information on the back:
Melissa Thornbury
Owner/CEO
info@rkpadvisory.net
www.rkpadvisory.net
555.302.9817

The front side should just have the company name incorporated: "RKP Advisory" and "virtual assistance"

The card should be simplistic, but eye catching and should speak to high level executives. Our primary focus areas consist of executive assistance and government contracting.

Target Market(s)

CEOs and executives

Contact Information for Business Card

see project description. phone, email, website.

Colors

Designer to choose only greyscale colors for use in the design.

```html
<!DOCTYPE html>
<html lang="en">
<head>
<meta charset="utf-8">
<title>RKP Advisory — Business Card</title>
<link rel="stylesheet" href="https://fonts.googleapis.com/css2?family=Sorts+Mill+Goudy&family=Libre+Caslon+Text:wght@700&family=Montserrat:wght@400&display=swap">
<style>
  :root {
    --backdrop: #d9d6d1;
    --card: #1c1c1c;
    --ink: #ffffff;
    --ink-soft: #e6e6e6;
    --shadow: rgba(0, 0, 0, 0.35);
  }
  * { margin: 0; padding: 0; box-sizing: border-box; }
  html, body {
    width: 900px;
    height: 1200px;
    overflow: hidden;
    background: var(--backdrop);
  }
  .canvas {
    position: relative;
    width: 900px;
    height: 1200px;
  }
  .card {
    position: absolute;
    left: 80px;
    width: 742px;
    height: 441px;
    background: var(--card);
    border-radius: 24px;
    box-shadow: 0 6px 18px var(--shadow);
    color: var(--ink);
  }
  .card--front { top: 131px; }
  .card--back { top: 640px; }

  .company-name {
    position: absolute;
    left: 34px;
    top: 36px;
    font-family: "Sorts Mill Goudy", serif;
    font-size: 46px;
    line-height: 1;
    letter-spacing: 0.2px;
  }
  .person {
    position: absolute;
    right: 52px;
    top: 48px;
    text-align: right;
  }
  .person-name {
    font-family: "Libre Caslon Text", serif;
    font-weight: 700;
    font-size: 24px;
    line-height: 1.1;
  }
  .person-title {
    font-family: "Montserrat", sans-serif;
    font-size: 15px;
    color: var(--ink-soft);
    margin-top: 4px;
  }
  .contact-list {
    position: absolute;
    left: 44px;
    top: 289px;
    list-style: none;
    font-family: "Montserrat", sans-serif;
    font-size: 16px;
  }
  .contact-item {
    display: flex;
    align-items: center;
    height: 28px;
  }
  .contact-icon {
    width: 16px;
    height: 16px;
    margin-right: 9px;
    fill: var(--ink);
  }
  .tagline {
    position: absolute;
    left: 45px;
    top: 391px;
    font-family: "Sorts Mill Goudy", serif;
    font-size: 16px;
    letter-spacing: 0.3px;
  }
  .brand-mark {
    position: absolute;
    font-family: "Sorts Mill Goudy", serif;
    color: var(--ink);
    line-height: 1;
  }
  .brand-mark--front {
    right: 38px;
    top: 222px;
    font-size: 112px;
  }
  .brand-mark--back {
    left: 0;
    right: 0;
    top: 110px;
    text-align: center;
    font-size: 190px;
  }
</style>
</head>
<body>
<main class="canvas">
  <section class="card card--front" aria-label="Card front">
    <h1 class="company-name">RKP Advisory</h1>
    <div class="person">
      <p class="person-name">Melissa Thornbury</p>
      <p class="person-title">Owner/CEO</p>
    </div>
    <ul class="contact-list">
      <li class="contact-item">
        <svg class="contact-icon" viewBox="0 0 24 24" aria-hidden="true"><path d="M6.6 10.8a15.1 15.1 0 0 0 6.6 6.6l2.2-2.2a1 1 0 0 1 1-.25 11.4 11.4 0 0 0 3.6.57 1 1 0 0 1 1 1V20a1 1 0 0 1-1 1A17 17 0 0 1 3 4a1 1 0 0 1 1-1h3.5a1 1 0 0 1 1 1c0 1.25.2 2.45.57 3.57a1 1 0 0 1-.25 1z"/></svg>
        <span>555.302.9817</span>
      </li>
      <li class="contact-item">
        <svg class="contact-icon" viewBox="0 0 24 24" aria-hidden="true"><path d="M3 6h18v12H3z M3 6l9 7 9-7" /><path d="M3 6l9 7 9-7" fill="none" stroke="#1c1c1c" stroke-width="1.6"/></svg>
        <span>info@rkpadvisory.net</span>
      </li>
      <li class="contact-item">
        <svg class="contact-icon" viewBox="0 0 24 24" aria-hidden="true"><circle cx="12" cy="12" r="9"/><path d="M3 12h18M12 3c3 3 3 15 0 18M12 3c-3 3-3 15 0 18" fill="none" stroke="#1c1c1c" stroke-width="1.4"/></svg>
        <span>www.rkpadvisory.net</span>
      </li>
    </ul>
    <p class="tagline">VIRTUAL ASSISTANCE</p>
    <p class="brand-mark brand-mark--front">RKP</p>
  </section>

  <section class="card card--back" aria-label="Card back">
    <p class="brand-mark brand-mark--back">RKP</p>
  </section>
</main>
</body>
</html>
```